Web site for radio show

I've got a radio show starting on OrbitalWave and need a web site for it. I am familiar with WordPress, so I'd like to get a design for a WordPress-based web site for the show.

I'm also posting a logo project to be done at the same time.

The best radio show web site I've seen is the Cosmic Tuesday site (www.cosmictuesday-example.com). That's a good model but I don't want to start with that much complexity and content. The initial site that I'd like you to design would have the following parts:
- Upcoming shows
- Past shows (including links to authors, their web sites, and their books)
- Feed feed
- Blog
- About
- ...and anything else you think would be necessary

For colors, I'd like it to be consistent with my personal web site: www.kellaway-ventures-example.com

Target Market(s)

The target market for this show is mid- to upper-level managers

Industry/Entity Type

Radio

Requirements
Must have
• The project has to proceed in (at least) two stages: a first rough layout, and a second finished design. Whether you want a third stage in between with look and feel options is up to you.

```html
<!DOCTYPE html>
<html lang="en">
<head>
<meta charset="utf-8">
<title>Kellaway Show</title>
<link href="https://fonts.googleapis.com/css2?family=Open+Sans:wght@400;600&family=Alegreya+Sans:wght@400;500&display=swap" rel="stylesheet">
<style>
:root{
  --red:#c8141c;
  --ink:#2b2b2b;
  --text:#3a3a3a;
  --page:#f6f6f6;
  --card:#ffffff;
  --rule:#d4d4d4;
  --navdark:#2e2e2e;
  --sky:#1aa3e0;
  --foot:#353639;
  --footbar:#2a2b2e;
  --foottext:#e4e4e4;
}
*{box-sizing:border-box;margin:0;padding:0}
html,body{width:788px;height:1200px;overflow:hidden}
body{background:var(--page);font-family:"Open Sans",Arial,sans-serif;color:var(--text);position:relative}
.abs{position:absolute}

/* header */
.brand{left:92px;top:18px;display:flex;align-items:center;gap:12px}
.brand-mark{width:40px;height:40px;border-radius:50%;border:2px solid #c9c9c9;background:#fff}
.brand-name{font-size:20px;color:var(--red);font-weight:400}
.date-card{top:0;height:74px;background:var(--card);border-bottom:3px solid var(--rule);text-align:center;padding-top:8px}
.date-card .d{font-size:20px;color:var(--ink);line-height:1.05}
.date-card .w{font-size:15px;color:var(--red);line-height:1.25}
.date-card .v{font-size:7.5px;color:#555;margin-top:2px}

.nav{left:82px;top:79px;height:36px;display:flex;font-size:10.5px}
.nav a{display:block;padding:0 13px;line-height:36px;color:#333;text-decoration:none}
.nav a.active{background:var(--navdark);color:#fff;padding:0 15px}

/* hero */
.hero{left:82px;top:131px;width:624px;height:263px;background:var(--card);padding:6px 5px}
.hero-stage{position:relative;width:100%;height:100%;background:radial-gradient(ellipse at 40% 30%,#fbfdff 0%,#dbeef8 45%,#9fd2ec 100%)}
.hero-kicker{left:1px;top:57px;width:224px;height:34px;background:#2c2c2c;color:var(--red);font-size:13.5px;line-height:34px;padding-left:13px}
.hero-title{left:1px;top:97px;width:169px;height:33px;background:#2c2c2c;color:#fff;font-size:18px;line-height:33px;padding-left:13px}
.hero-copy{left:14px;top:145px;width:246px;font-size:8.3px;line-height:14.5px;letter-spacing:.4px;text-align:justify}
.hero-photo{left:381px;top:30px;width:140px;height:194px;background:#fff;padding:4px;transform:rotate(5deg);box-shadow:0 2px 6px rgba(0,0,0,.25)}
.hero-photo div{width:100%;height:100%;background:linear-gradient(160deg,#d8c38a 0%,#8a7a4e 40%,#2b2a24 70%,#6b6a58 100%)}
.dots{left:283px;top:237px;display:flex;gap:3px}
.dots i{width:6px;height:6px;border-radius:50%;background:#fff}
.dots i.on{background:var(--red)}

/* shows */
.sec-title{font-size:17px;color:var(--ink);font-weight:400}
.sec-title b{font-weight:600}
.show{width:310px;height:72px}
.show-date{left:0;top:0;width:84px;height:72px;background:var(--card);border-bottom:3px solid var(--rule);text-align:center;padding-top:9px}
.show-date .d{font-size:19px;color:var(--ink);line-height:1.05}
.show-date .w{font-size:14px;color:var(--red);line-height:1.3}
.show-date .v{font-size:7.3px;color:#555}
.show-thumb{left:0;top:0;width:90px;height:63px}
.show-body{left:95px;top:0;width:212px}
.show-body h3{font-size:12.5px;color:var(--red);font-weight:400;margin-bottom:5px}
.show-body p{font-size:8.3px;line-height:13.8px;color:#333}
.show-body em{font-weight:600;color:#222}

.dotted{left:82px;top:698px;width:624px;border-top:3px dotted #b8b8b8}

.about-box{left:82px;top:740px;width:409px;height:157px;background:var(--card);padding:10px 10px}
.about-photo{left:10px;top:10px;width:70px;height:69px;background:linear-gradient(135deg,#3c5a8a,#c08a6a 55%,#2a4070)}
.about-lead{margin-left:82px;font-size:7.6px;line-height:12.4px;text-align:justify;height:72px}
.about-rest{font-size:7.6px;line-height:12.4px;text-align:justify;margin-top:7px}
.blog-box{left:509px;top:740px;width:197px;height:157px;background:var(--card);padding:10px 14px 0 43px;font-size:7.6px;line-height:12.4px;text-align:justify}
.quote{left:12px;top:4px;font-size:34px;color:#bbb;font-family:Georgia,serif}

/* feed band */
.feed{left:0;top:921px;width:788px;height:66px;background:var(--sky)}
.feed-dot{left:88px;top:23px;width:20px;height:20px;border-radius:50%;background:#fff}
.feed-text{left:130px;top:25px;font-family:"Alegreya Sans",sans-serif;font-size:12px;color:#fff}
.feed-btn{left:646px;top:26px;width:60px;height:17px;background:#166b9c;color:#fff;font-size:6.8px;text-align:center;line-height:17px}

/* footer */
.footer{left:0;top:987px;width:788px;height:180px;background:var(--foot);font-family:"Alegreya Sans",sans-serif;color:var(--foottext)}
.fcol{top:24px}
.fcol h4{font-size:13px;font-weight:400;margin-bottom:10px;color:#f0f0f0}
.fcol li{list-style:none;font-size:8.3px;line-height:13.8px}
.contact p{font-size:8.3px;line-height:13.8px}
.socials{display:flex;gap:8px;margin-top:9px}
.socials i{width:6px;height:6px;border-radius:50%;background:#9a9a9a}
.partner{margin-top:18px;width:115px;height:31px;background:#fff;border-radius:4px;display:flex;align-items:center;justify-content:center;font-size:14px;color:#1f3f8f;font-weight:500}
.bottom{left:0;top:1167px;width:788px;height:33px;background:var(--footbar);font-family:"Alegreya Sans",sans-serif;font-size:8.3px;color:#ddd}
.red-tab{left:741px;top:640px;width:44px;height:15px;background:var(--red);border-radius:2px}
</style>
</head>
<body>

<header>
  <div class="abs brand"><span class="brand-mark"></span><span class="brand-name">Kellaway Show</span></div>
  <div class="abs date-card" style="left:430px;width:66px"><div class="d">5 MAR</div><div class="w">Monday</div><div class="v">Club Galaxy</div></div>
  <div class="abs date-card" style="left:522px;width:84px"><div class="d">24 APR</div><div class="w">Tuesday</div><div class="v">Kudos Beach</div></div>
  <div class="abs date-card" style="left:614px;width:84px"><div class="d">9 AUG</div><div class="w">Saturday</div><div class="v">Stormfront Festival</div></div>
  <nav class="abs nav">
    <a class="active">Home</a><a>Blog</a><a>Events</a><a>Audio</a><a>Photos</a><a>Artists</a><a>DJ Mixes</a><a>About</a>
  </nav>
</header>

<section class="abs hero">
  <div class="hero-stage">
    <div class="abs hero-kicker">Welcome to the mainpage of</div>
    <div class="abs hero-title">Kellaway Show</div>
    <p class="abs hero-copy">Lorem ipsum dolor sit amet, consectetur adipiscing elit. Donec vulputate lacinia diam, eu mollis odio varius sodales. Phasellus pellentesque.</p>
    <div class="abs hero-photo"><div role="img" aria-label="Photo of a studio microphone in close-up"></div></div>
    <div class="abs dots"><i></i><i></i><i class="on"></i><i></i><i></i></div>
  </div>
</section>

<h2 class="abs sec-title" style="left:88px;top:408px">Upcoming <b>Shows</b></h2>
<h2 class="abs sec-title" style="left:403px;top:408px">Past <b>Shows</b></h2>

<div class="abs show" style="left:88px;top:439px">
  <div class="abs show-date"><div class="d">5 MAR</div><div class="w">Monday</div><div class="v">Club Galaxy</div></div>
  <div class="abs show-body"><h3>Show Title Here</h3><p>Nulla dui purus, eleifend vel, consequat non, dictum porta, nulla. Duis ante mi, laoreet ut, commodo eleif-end, cursus nec, lorem.<em>Read More</em></p></div>
</div>
<div class="abs show" style="left:88px;top:522px">
  <div class="abs show-date"><div class="d">24 APR</div><div class="w">Tuesday</div><div class="v">Kudos Beach</div></div>
  <div class="abs show-body"><h3>Show Title Here</h3><p>Nulla dui purus, eleifend vel, consequat non, dictum porta, nulla. Duis ante mi, laoreet ut, commodo eleif-end, cursus nec, lorem. <em>Read More</em></p></div>
</div>
<div class="abs show" style="left:88px;top:607px">
  <div class="abs show-date"><div class="d">9 AUG</div><div class="w">Saturday</div><div class="v">Stormfront Festival</div></div>
  <div class="abs show-body"><h3>Show Title Here</h3><p>Nulla dui purus, eleifend vel, consequat non, dictum porta, nulla. Duis ante mi, laoreet ut, commodo eleif-end, cursus nec, lorem.<em>Read More</em></p></div>
</div>

<div class="abs show" style="left:402px;top:441px">
  <div class="abs show-thumb" role="img" aria-label="Photo of a radio studio mixing desk with microphone" style="background:linear-gradient(135deg,#5a7fa8,#2e3440 55%,#8a8f96)"></div>
  <div class="abs show-body" style="top:-2px"><h3>Show Title Here</h3><p>Nulla dui purus, eleifend vel, consequat non, dictum porta, nulla. Duis ante mi, laoreet ut, commodo eleif-end, cursus nec, lorem.<em>Read More</em></p></div>
</div>
<div class="abs show" style="left:402px;top:523px">
  <div class="abs show-thumb" role="img" aria-label="Photo of two radio hosts at the studio microphone" style="background:linear-gradient(135deg,#3a3328,#a07a5c 50%,#c9a0a8)"></div>
  <div class="abs show-body" style="top:-1px"><h3>Show Title Here</h3><p>Nulla dui purus, eleifend vel, consequat non, dictum porta, nulla. Duis ante mi, laoreet ut, commodo eleif-end, cursus nec, lorem. <em>Read More</em></p></div>
</div>
<div class="abs show" style="left:402px;top:607px">
  <div class="abs show-thumb" role="img" aria-label="Photo of a lit on-air studio sign" style="width:88px;height:70px;background:radial-gradient(circle,#e8401c,#a40e0c 60%,#2a0a06)"></div>
  <div class="abs show-body" style="top:2px"><h3>Show Title Here</h3><p>Nulla dui purus, eleifend vel, consequat non, dictum porta, nulla. Duis ante mi, laoreet ut, commodo eleif-end, cursus nec, lorem.<em>Read More</em></p></div>
</div>

<div class="abs red-tab"></div>
<div class="abs dotted"></div>

<h2 class="abs sec-title" style="left:91px;top:711px">About</h2>
<h2 class="abs sec-title" style="left:514px;top:711px">Blog <b>Posts</b></h2>

<section class="abs about-box">
  <div class="abs about-photo" role="img" aria-label="Portrait photo of the show host in the studio"></div>
  <p class="about-lead">Nulla dui purus, eleifend vel, consequat non, dictum porta, nulla. Duis ante mi, laoreet ut, commodo eleifend, cursus nec, lorem. Aenean eu est. Etiam imperdiet turpis. Praesent nec augue. Nulla dui purus, eleifend vel, consequat non, dictum porta, nulla. Duis ante mi, laoreet ut, commodo eleifend, cursus nec, lorem. Aenean eu est. Etiam imperdiet turpis. Praesent nec augue.Nulla dui purus, eleifend vel, ulla. Nulla dui purus, eleifend vel, consequat non, dictum porta, nulla.</p>
  <p class="about-rest">Duis ante mi, laoreet ut, commodo eleifend, cursus nec, lorem. Aenean eu est. Etiam imperdiet turpis. Praesent nec augue. Nulla dui purus, eleifend vel, consequat non, dictum porta, nulla. Duis ante mi, laoreet ut, commodo eleifend, cursus nec, lorem. Aenean eu est. Etiam imperdiet turpis. Praesent nec augue.Nulla dui purus, eleifend vel, ulla. Nulla dui purus, eleifend vel, consequat non, dictum porta, nulla.</p>
</section>

<section class="abs blog-box">
  <span class="abs quote">&ldquo;</span>
  <p>Nulla dui purus, eleifend vel, consequat non, dictum porta, nulla. Duis ante mi, laoreet ut, commodo eleifend, cursus nec, lorem. Aenean eu est. Etiam imperdiet turpis. Praesent nec augue. Nulla dui purus, eleifend vel, consequat non, dictum porta, nulla. Duis ante mi, laoreet ut, commodo eleifend, cursus nec, lorem. Aenean eu est. Etiam imperdiet turpis. Praesent nec augue.Nulla dui</p>
</section>

<section class="abs feed">
  <span class="abs feed-dot"></span>
  <p class="abs feed-text">There are many variations of passages of Lorem Ipsum available, but the majority have suffered alteration.</p>
  <span class="abs feed-btn">Follow Us</span>
</section>

<footer class="abs footer">
  <div class="abs fcol" style="left:82px"><h4>Quick Links</h4><ul><li>Home</li><li>About Us</li><li>Services</li><li>Ordering</li><li>Support</li><li>News</li><li>Testimonials</li><li>Contact Us</li></ul></div>
  <div class="abs fcol" style="left:187px"><h4>Support Links</h4><ul><li>Home</li><li>About Us</li><li>Services</li><li>Ordering</li><li>Support</li><li>News</li><li>Testimonials</li><li>Contact Us</li></ul></div>
  <div class="abs fcol" style="left:299px"><h4>Latest Blog Posts</h4><ul><li>Introduction</li><li>About Us</li><li>Services</li><li>Ordering</li><li>Support</li><li>News</li><li>Testimonials</li><li>Contact Us</li></ul></div>
  <div class="abs fcol" style="left:420px"><h4>Support Links</h4><ul><li>Home</li><li>About Us</li><li>Services</li><li>Ordering</li><li>Support</li><li>News</li><li>Testimonials</li><li>Contact Us</li></ul></div>
  <div class="abs fcol contact" style="left:522px"><h4>Contact Us</h4>
    <p>Sector 9, Harbor Villa, Lanton Street, Westfield.</p>
    <p>Tel : +15 0000 555 0142 , Fax : +15 0000 555 0143</p>
    <p>info@showcompany-example.com</p>
    <div class="socials"><i></i><i></i><i></i><i></i><i></i><i></i><i></i><i></i><i></i><i></i><i></i></div>
    <div class="partner">OrbitalWave</div>
  </div>
</footer>

<div class="abs bottom">
  <span class="abs" style="left:82px;top:11px">Copyright &copy; 2002-2014 ShowCompany. All rights reserved.</span>
  <span class="abs" style="left:586px;top:11px">Privacy Policy &nbsp;&nbsp; Legal &nbsp;&nbsp; Disclaimer</span>
</div>

</body>
</html>
```